Animal Eye Clinic needs a Business card

We are a new veterinary ophthalmology practice (Ridgeline Pet Vision Care) and we need a business card designed. We only see animal eyes - we are not a regular veterinary clinic. We already have a logo. We are looking for a professional, good looking business card to hand out to our clients. We are looking for something simple but professional and contemporary. Our logo is likely the only picture/graphic that needs to be on the card.
Updates

Contact Information for Business Card

Delia Vossman, BSc, DVM, MSc, DipACVO
Veterinary Ophthalmologist

Phone: 250.418.3927
Email: ridgelinepetvisioncare@mailbox-example.net
Website: ridgelinepetvisioncare-example.net
Address: 1874 Thornbury Rd
Kelowna, BC, V1X 4M9

Colors

Designer to choose colors to be used in the design.

Requirements
Must have
• Our logo (attached)

```html
<!DOCTYPE html>
<html lang="en">
<head>
<meta charset="utf-8">
<title>Ridgeline Pet Vision Care — Business Card</title>
<link rel="stylesheet" href="https://fonts.googleapis.com/css2?family=Arimo:wght@400;700&family=Roboto+Condensed:wght@400;700&display=swap">
<style>
  :root {
    --backdrop: #2b2929;
    --card: #f2f2f2;
    --card-edge: #e6e6e6;
    --teal: #0898ab;
    --grey-text: #5a5a5a;
    --grey-soft: #7d7d7d;
  }
  * { margin: 0; padding: 0; box-sizing: border-box; }
  html, body {
    width: 1125px; height: 1200px; overflow: hidden;
    background: var(--backdrop);
  }
  .canvas { position: relative; width: 1125px; height: 1200px; }

  .card {
    position: absolute; left: 167px; width: 790px; height: 450px;
    background: linear-gradient(180deg, var(--card) 0%, var(--card-edge) 100%);
    overflow: hidden;
  }
  .card--front { top: 115px; border-radius: 225px 0 0 225px; }
  .card--back  { top: 648px; border-radius: 0 225px 225px 0; }

  /* front */
  .logo-area { position: absolute; left: 20px; top: 25px; width: 380px; height: 380px; }
  .contact {
    position: absolute; left: 419px; top: 128px;
    font-family: "Arimo", Arial, sans-serif; color: var(--grey-text);
  }
  .contact__name {
    font-family: "Roboto Condensed", "Arial Narrow", sans-serif;
    font-weight: 700; font-size: 20px; color: var(--teal); letter-spacing: 0.3px;
  }
  .contact__creds { font-size: 14px; font-weight: 700; }
  .contact__role { font-size: 16px; color: var(--grey-soft); margin-top: 4px; }
  .contact__address { font-size: 17px; line-height: 23px; margin-top: 17px; }
  .contact__list { list-style: none; margin-top: 10px; font-size: 16px; line-height: 23px; }
  .contact__list li { display: flex; align-items: center; gap: 10px; }
  .contact__list svg { width: 13px; height: 13px; flex: none; fill: var(--teal); }

  /* back */
  .brand {
    position: absolute; left: 95px; top: 0; height: 450px;
    display: flex; align-items: center; gap: 24px;
  }
  .brand__dot { width: 72px; height: 72px; border-radius: 50%; background: var(--teal); flex: none; }
  .brand__name {
    font-family: "Arimo", Arial, sans-serif; font-weight: 700;
    font-size: 40px; line-height: 46px; color: var(--teal); text-transform: uppercase;
  }
</style>
</head>
<body>
<main class="canvas">

  <section class="card card--front">
    <svg class="logo-area" viewBox="0 0 380 380" role="img" aria-label="Clinic logo artwork: horse, dog and cat silhouettes in a circle">
      <circle cx="190" cy="190" r="190" fill="#0898ab"/>
    </svg>

    <div class="contact">
      <p class="contact__name">DELIA VOSSMAN, <span class="contact__creds">BSc, DVM, MSc, DipACVO</span></p>
      <p class="contact__role">Veterinary Ophthalmologist</p>
      <p class="contact__address">1874 Thornbury Rd<br>Kelowna, BC, V1X 4M9</p>
      <ul class="contact__list">
        <li>
          <svg viewBox="0 0 16 16" aria-hidden="true"><path d="M3.5 1 6 4 4.8 6a9 9 0 0 0 5.2 5.2L12 10l3 2.5-1.6 2.3C7.5 15 1 8.5 1.2 2.6Z"/></svg>
          250.418.3927
        </li>
        <li>
          <svg viewBox="0 0 16 16" aria-hidden="true"><path d="M1 3h14v10H1Zm1.5 1.3v.3L8 8.6l5.5-4v-.3Z"/></svg>
          ridgelinepetvisioncare@mailbox-example.net
        </li>
        <li>
          <svg viewBox="0 0 16 16" aria-hidden="true"><path d="M8 1a7 7 0 1 0 0 14A7 7 0 0 0 8 1Zm-1 2.5 2 1.5-1 2 2 1.5-1 3.5-2-2V8L5 6.5Z"/></svg>
          ridgelinepetvisioncare-example.net
        </li>
      </ul>
    </div>
  </section>

  <section class="card card--back">
    <div class="brand">
      <span class="brand__dot" aria-hidden="true"></span>
      <p class="brand__name">Ridgeline<br>Pet Vision Care</p>
    </div>
  </section>

</main>
</body>
</html>
```